Webdesign für Hersteller für Pack- und Palettieranlagen für den Getränke- und Lebensmittelbereich
Webdesign für Hersteller für Pack- und Palettieranlagen für den Getränke- und Lebensmittelbere..
Zielgruppe
Hersteller für Pack- und Palettieranlagen für den Getränke- und Lebensmittelbereich
Zielgruppe: Getränke- und Lebensmittelhersteller
Aufgabenstellung
die zukünftige Seite soll dynamischer und intuitiver werden
klare Strukturen, aber morderner als das jetztige Layout
Keine Kopie der alten Seite www.kolmatech.de!
Startseite soll aufgeräumter sein
Logo, Rufnummer, Mail, Social Media
Startseite mit großem Headerbild (Slider)

```html
<!DOCTYPE html>
<html lang="de">
<head>
<meta charset="utf-8">
<title>KOLMATECH Maschinenbau</title>
<link rel="stylesheet" href="https://fonts.googleapis.com/css2?family=Open+Sans:wght@400;600;700;800&display=swap">
<style>
:root{
  --green:#6ab42d;
  --orange:#f39325;
  --dark:#3c3c3c;
  --text:#333;
  --muted:#666;
  --grey-band:#efefef;
  --footer:#3a3a3a;
  --white:#fff;
}
*{box-sizing:border-box;margin:0;padding:0}
html,body{width:1200px;height:3325px;overflow:hidden}
body{font-family:"Open Sans",Arial,sans-serif;color:var(--text);background:var(--white);position:relative}
.abs{position:absolute}
.section-title{position:absolute;left:0;width:1200px;text-align:center;font-size:19px;font-weight:700;color:#444;letter-spacing:.3px}

/* header */
.brand{left:75px;top:34px;display:flex;align-items:center;gap:8px}
.brand-dot{width:24px;height:24px;border-radius:50%;background:var(--green)}
.brand-name{font-size:27px;font-weight:800;color:var(--green);line-height:1}
.brand-sub{font-size:11px;font-weight:700;color:#333;display:block;text-align:right;margin-top:1px}
.pill{top:45px;height:32px;border-radius:16px;background:var(--green);color:#fff;font-size:12px;display:flex;align-items:center;gap:8px;padding:0 14px}
.social{top:53px;display:flex;gap:13px;left:1028px}
.social span{width:14px;height:14px;border-radius:50%;background:#777}
.nav{top:116px;left:0;width:1200px;display:flex;justify-content:center;gap:25px;font-size:13px;font-weight:500;color:#222}
.nav a{color:inherit;text-decoration:none}

/* hero */
.hero{top:150px;left:0;width:1200px;height:499px;background:linear-gradient(135deg,#3a4656 0%,#5d7a96 35%,#2f6aa8 55%,#2a3038 100%)}
.hero h1{position:absolute;left:75px;top:338px;font-size:52px;line-height:50px;font-weight:700;color:#fff}
.dots{display:flex;gap:12px;justify-content:center;position:absolute;left:0;width:1200px}
.dots span{width:6px;height:6px;border-radius:50%;background:#ccc}
.hero .dots span{background:#fff}

/* categories */
.cat{top:757px;width:151px;height:135px;background:#fff;border-radius:4px;box-shadow:0 2px 10px rgba(0,0,0,.08);text-align:center;padding-top:20px}
.cat svg{display:block;margin:0 auto}
.cat h3{font-size:11px;font-weight:600;color:var(--green);margin-top:12px;padding-bottom:6px;border-bottom:1px solid #e8e8e8;margin-left:12px;margin-right:12px}
.cat p{font-size:9px;color:#555;margin-top:8px;line-height:10px}
.cat.active{background:var(--green)}
.cat.active h3,.cat.active p{color:#fff;border-color:#fff}
.machine{top:929px;width:235px;height:252px;background:#fff;box-shadow:0 4px 18px rgba(0,0,0,.1);text-align:center}
.machine .ph{width:145px;height:187px;margin:22px auto 0}
.machine h4{font-size:13px;font-weight:600;color:#333;margin-top:14px;letter-spacing:.3px}

/* news */
.band{top:1245px;left:0;width:1200px;height:561px;background:var(--grey-band)}
.news{top:1339px;width:280px}
.news .ph{height:248px;background:#fff;border-radius:3px;box-shadow:0 3px 14px rgba(0,0,0,.08)}
.news .meta{display:flex;justify-content:space-between;font-size:7px;color:#666;margin-top:10px}
.news h4{font-size:11px;font-weight:700;margin-top:10px;color:#333}
.news p{font-size:8.4px;line-height:9.4px;color:#555;margin-top:13px}
.share{width:31px;height:29px;border-radius:4px;background:var(--orange);margin-top:13px;display:flex;align-items:center;justify-content:center}

/* jobs */
.intro{top:1910px;left:300px;width:600px;text-align:center;font-size:10.5px;line-height:11px;color:#444}
.tabs{top:1970px;left:0;width:1200px;display:flex;justify-content:center;gap:36px;font-size:11px;color:#444}
.tabs .on{color:var(--green);border-bottom:1px solid var(--green);padding-bottom:5px}
.job{top:2058px;width:427px;height:147px;background:var(--dark);border-radius:3px;color:#fff;padding:10px 13px;box-shadow:0 3px 10px rgba(0,0,0,.2)}
.job .meta{display:flex;justify-content:space-between;font-size:7px;color:#ddd}
.job h4{font-size:11px;font-weight:400;line-height:15px;margin-top:9px}
.job .role{font-size:9px;margin-top:11px}
.job .btns{display:flex;gap:13px;margin-top:14px}
.btn{height:31px;border-radius:2px;font-size:10px;font-weight:700;display:flex;align-items:center;justify-content:center;color:#fff}
.btn.out{width:95px;border:1px solid #ddd}
.btn.or{width:137px;margin-left:auto;background:var(--orange)}
.btn.gr{width:93px;background:var(--green)}

/* company */
.about{top:2442px;left:77px;width:460px;font-size:10.6px;line-height:11px;color:#444}
.about p{margin-bottom:12px}

/* contact */
.contact{top:2737px;left:67px;width:1066px;height:341px;background:#fff;box-shadow:0 4px 20px rgba(0,0,0,.1)}
.contact .ph{position:absolute;left:0;top:0;width:506px;height:341px;background:linear-gradient(160deg,#3a4b66,#5b6e8e 40%,#8a7a58 70%,#2c3140)}
.contact h2{position:absolute;left:556px;top:38px;font-size:19px;font-weight:700;color:#444}
.field{position:absolute;width:170px;border-bottom:1px solid #ccc;font-size:10.5px;color:#555;padding-bottom:3px}
.send{position:absolute;left:556px;top:282px;width:93px;height:30px;background:var(--green);border-radius:2px;color:#fff;font-size:10px;font-weight:700;display:flex;align-items:center;justify-content:center;gap:10px}

/* footer */
.footer{top:3157px;left:0;width:1200px;height:168px;background:var(--footer);color:#fff}
.footer h5{position:absolute;font-size:10.5px;font-weight:700}
.footer .col{position:absolute;font-size:9px;line-height:20px}
.footer .copy{position:absolute;left:0;top:121px;width:1200px;border-top:1px solid #555;text-align:center;font-size:9px;padding-top:16px}
.news-form{position:absolute;left:951px;top:42px;font-size:8px}
.news-form .box{display:flex;margin-top:8px}
.news-form .in{width:124px;height:25px;background:#fff;color:#555;font-size:8px;padding:8px 10px;border-radius:2px 0 0 2px}
.news-form .go{width:31px;height:25px;background:var(--green);display:flex;align-items:center;justify-content:center}
</style>
</head>
<body>

<!-- header -->
<div class="abs brand">
  <span class="brand-dot"></span>
  <div><span class="brand-name">KOLMATECH</span><span class="brand-sub">Maschinenbau GmbH</span></div>
</div>
<div class="abs pill" style="left:728px;width:131px">
  <svg width="11" height="11" viewBox="0 0 24 24"><path fill="#fff" d="M6.6 10.8a15 15 0 0 0 6.6 6.6l2.2-2.2c.3-.3.7-.4 1-.2 1.1.4 2.3.6 3.6.6.6 0 1 .4 1 1V20c0 .6-.4 1-1 1A17 17 0 0 1 3 4c0-.6.4-1 1-1h3.5c.6 0 1 .4 1 1 0 1.3.2 2.5.6 3.6.1.3 0 .7-.2 1z"/></svg>03400 / 200 - 0</div>
<div class="abs pill" style="left:881px;width:126px">
  <svg width="12" height="10" viewBox="0 0 24 18"><rect x="1" y="1" width="22" height="16" rx="2" fill="#fff"/><path d="M2 2l10 8 10-8" stroke="#6ab42d" stroke-width="2" fill="none"/></svg>info@kolmatech.de</div>
<div class="abs social"><span></span><span></span><span></span><span></span></div>
<nav class="abs nav">
  <a>UNTERNEHMEN</a><a>JOBS / KARRIERE</a><a>PALETTIERTECHNIK</a><a>PACKERTECHNIK</a><a>FÖRDERTECHNIK</a><a>ANLAGEN</a><a>GEBRAUCHTMASCHINEN</a><a>AKTUELLES</a>
</nav>

<!-- hero -->
<section class="abs hero" role="img" aria-label="Verpackungsanlage mit in Folie eingeschweißten Gebinden auf einem Förderband">
  <h1>Getränke- und<br>Lebensmittelproduktionstechnik</h1>
  <div class="dots" style="top:475px"><span></span><span></span><span></span><span></span><span></span></div>
</section>

<!-- products -->
<h2 class="section-title" style="top:686px">PRODUKTE</h2>
<div class="abs cat active" style="left:239px">
  <svg width="46" height="30" viewBox="0 0 46 30"><path d="M4 18l19-10 19 10-19 10z" fill="#fff"/><path d="M4 12l19-10 19 10-19 10z" fill="#fff" opacity=".8"/></svg>
  <h3>PALETTIERTECHNIK</h3><p>ProPal<br>Unsere Palettierfamilie</p>
</div>
<div class="abs cat" style="left:430px">
  <svg width="40" height="40" viewBox="0 0 40 40"><path d="M8 18h24v18H8z" fill="#6ab42d"/><path d="M14 6h12v10H14z" fill="#6ab42d"/></svg>
  <h3>PACKERTECHNIK</h3><p>ProPac<br>Unsere Flaschenpacker</p>
</div>
<div class="abs cat" style="left:619px">
  <svg width="46" height="32" viewBox="0 0 46 32"><rect x="2" y="2" width="10" height="9" fill="#6ab42d"/><rect x="18" y="2" width="10" height="9" fill="#6ab42d"/><rect x="34" y="2" width="10" height="9" fill="#6ab42d"/><rect x="2" y="14" width="42" height="14" rx="3" fill="#6ab42d"/><circle cx="12" cy="21" r="3" fill="#fff"/><circle cx="23" cy="21" r="3" fill="#fff"/><circle cx="34" cy="21" r="3" fill="#fff"/></svg>
  <h3>FÖRDERTECHNIK</h3><p>ProTrans<br>Behälter- Und<br>Gebindetransport</p>
</div>
<div class="abs cat" style="left:809px">
  <svg width="40" height="34" viewBox="0 0 40 34"><circle cx="16" cy="15" r="11" fill="#6ab42d"/><circle cx="16" cy="15" r="4" fill="#fff"/><circle cx="29" cy="26" r="6" fill="#6ab42d"/></svg>
  <h3>GEBRAUCHTMASCHINEN</h3><p>Alte Arbeitsmaschinen</p>
</div>

<div class="abs machine" style="left:76px"><div class="ph" role="img" aria-label="Technische Darstellung einer Portalmaschine" style="background:linear-gradient(160deg,#7bb86a,#3f8a3a 60%,#8a3a2a)"></div><h4>PORTALMASCHINEN</h4></div>
<div class="abs machine" style="left:347px"><div class="ph" role="img" aria-label="Technische Darstellung einer Einsäulenmaschine" style="background:linear-gradient(180deg,#fff 5%,#3c6fb0 30%,#2a4f88 80%,#fff)"></div><h4>EINSÄULENMASCHINEN</h4></div>
<div class="abs machine" style="left:618px"><div class="ph" role="img" aria-label="Industrieroboter mit Rollenförderbahn" style="background:linear-gradient(160deg,#d8dad2,#a8b49a 50%,#bfc4b6)"></div><h4>INDUSTRIEROBOTER</h4></div>
<div class="abs machine" style="left:889px"><div class="ph" role="img" aria-label="Technische Darstellung einer Neuglasmaschine" style="background:linear-gradient(160deg,#c75a7a,#3d7db5 40%,#e58a3a 70%,#7ab07a)"></div><h4>NEUGLASMASCHINEN</h4></div>

<!-- news -->
<section class="abs band"></section>
<h2 class="section-title" style="top:1274px">AKTUELLES</h2>
<article class="abs news" style="left:76px">
  <div class="ph" role="img" aria-label="Bild zur Meldung"></div>
  <div class="meta"><span>März 7, 2024</span><span>By KOLMATECH</span></div>
  <h4>Neue Abfüllanlage für Quellhof Limo</h4>
  <p>Lorem Ipsum Dolor Sit Amet, Consectetur Adipiscing Elit, Sed Do Eiusmod Tempor Incididunt Ut Labore Et Dolore Magna Aliqua. Ut Enim Ad Minim Veniam, Quis Nostrud Exercitation Ullamco Laboris Nisi Ut Aliquip Ex Ea Commodo Consequat. Duis Aute Irure Dolor In Reprehenderit In Voluptate Velit Esse Cillum Dolore Eu Fugiat Nulla Pariatur. Excepteur Sint Occaecat Cupidatat Non Proident, Sunt In Culpa Qui Officia Deserunt Mollit Anim Id Est Laborum.</p>
  <div class="share"><svg width="14" height="14" viewBox="0 0 24 24"><circle cx="18" cy="5" r="3" fill="#fff"/><circle cx="6" cy="12" r="3" fill="#fff"/><circle cx="18" cy="19" r="3" fill="#fff"/><path d="M6 12l12-7M6 12l12 7" stroke="#fff" stroke-width="2"/></svg></div>
</article>
<article class="abs news" style="left:460px">
  <div class="ph" role="img" aria-label="Bild zur Meldung"></div>
  <div class="meta"><span>März 7, 2024</span><span>By KOLMATECH</span></div>
  <h4>Neue Abfüllanlage für Quellhof Limo</h4>
  <p>Lorem Ipsum Dolor Sit Amet, Consectetur Adipiscing Elit, Sed Do Eiusmod Tempor Incididunt Ut Labore Et Dolore Magna Aliqua. Ut Enim Ad Minim Veniam, Quis Nostrud Exercitation Ullamco Laboris Nisi Ut Aliquip Ex Ea Commodo Consequat. Duis Aute Irure Dolor In Reprehenderit In Voluptate Velit Esse Cillum Dolore Eu Fugiat Nulla Pariatur. Excepteur Sint Occaecat Cupidatat Non Proident, Sunt In Culpa Qui Officia Deserunt Mollit Anim Id Est Laborum.</p>
  <div class="share"><svg width="14" height="14" viewBox="0 0 24 24"><circle cx="18" cy="5" r="3" fill="#fff"/><circle cx="6" cy="12" r="3" fill="#fff"/><circle cx="18" cy="19" r="3" fill="#fff"/><path d="M6 12l12-7M6 12l12 7" stroke="#fff" stroke-width="2"/></svg></div>
</article>
<article class="abs news" style="left:844px">
  <div class="ph" role="img" aria-label="Bild zur Meldung"></div>
  <div class="meta"><span>März 7, 2024</span><span>By KOLMATECH</span></div>
  <h4>Neue Abfüllanlage für Quellhof Limo</h4>
  <p>Lorem Ipsum Dolor Sit Amet, Consectetur Adipiscing Elit, Sed Do Eiusmod Tempor Incididunt Ut Labore Et Dolore Magna Aliqua. Ut Enim Ad Minim Veniam, Quis Nostrud Exercitation Ullamco Laboris Nisi Ut Aliquip Ex Ea Commodo Consequat. Duis Aute Irure Dolor In Reprehenderit In Voluptate Velit Esse Cillum Dolore Eu Fugiat Nulla Pariatur. Excepteur Sint Occaecat Cupidatat Non Proident, Sunt In Culpa Qui Officia Deserunt Mollit Anim Id Est Laborum.</p>
  <div class="share"><svg width="14" height="14" viewBox="0 0 24 24"><circle cx="18" cy="5" r="3" fill="#fff"/><circle cx="6" cy="12" r="3" fill="#fff"/><circle cx="18" cy="19" r="3" fill="#fff"/><path d="M6 12l12-7M6 12l12 7" stroke="#fff" stroke-width="2"/></svg></div>
</article>
<div class="dots" style="top:1772px"><span style="background:var(--orange)"></span><span style="background:#999"></span><span style="background:#999"></span><span style="background:#999"></span><span style="background:#999"></span></div>

<!-- jobs -->
<h2 class="section-title" style="top:1860px">JOBS / KARRIERE</h2>
<p class="abs intro">Schauen Sie Sich Jetzt Unsere Aktuellen Stellenangebote An Und Bewerben Sie Sich Ganz Einfach Auf Ihre Wunschstelle. Eine Bewerbung Läuft Ganz Einfach In 60 Sekunden Ab – Ohne Lebenslauf Oder Anschreiben.</p>
<div class="abs tabs"><span class="on">Alle Jobs</span><span>Development</span><span>Marketing</span><span>Specialist</span></div>
<div class="abs job" style="left:126px">
  <div class="meta"><span>März 7, 2024</span><span>Talheim, Germany</span></div>
  <h4>Für Die Fertigung Unserer Einzel- Und Serienprodukte Im Bereich Getränkemaschinenbau Suchen Wir Eine/N Fachlich Versierte/N</h4>
  <p class="role">SPS-Programmierer/In M/W/D</p>
  <div class="btns"><span class="btn out">€100K</span><span class="btn or">Stellenbeschreibung</span><span class="btn gr">Bewerben</span></div>
</div>
<div class="abs job" style="left:646px">
  <div class="meta"><span>März 7, 2024</span><span>Talheim, Germany</span></div>
  <h4>Für Die Fertigung Unserer Einzel- Und Serienprodukte Im Bereich Getränkemaschinenbau Suchen Wir Eine/N Fachlich Versierte/N</h4>
  <p class="role">SPS-Programmierer/In M/W/D</p>
  <div class="btns"><span class="btn out">N/A</span><span class="btn or">Stellenbeschreibung</span><span class="btn gr">Bewerben</span></div>
</div>
<div class="dots" style="top:2254px"><span style="background:var(--green)"></span><span></span><span></span><span></span><span></span></div>

<!-- company -->
<h2 class="section-title" style="top:2335px">UNTERNEHMEN</h2>
<div class="abs about">
  <p>Das Traditionsreiche Familienunternehmen Kolmatech Plant, Entwickelt Und Baut Pack- Und Palettieranlagen Für Den Getränke- Und Lebensmittelbereich. Mit Erfahrung Und Know-How Planen Und Konstruieren Wir Moderne Und Effiziente Anlagen, Die Optimal Auf Die Bedürfnisse Unserer Kunden Abgestimmt Sind.</p>
  <p>Wir Bieten Ihnen Individuelle Maschinen Und Anlagen Zur Abfüllung Und Verpackung, Sortier- Und Umpackanlagen Sowie Einen Umfassenden Rundum-Service An. Mit Unseren Weitläufigen Produktionsstätten Sind Wir In Der Lage, Die Vorarbeiten Der Montage Unter Unserem Dach Zu Erledigen, Sodass Der Zeitaufwand Für Den Aufbau Bei Ihnen Vor Ort Gering Ist.</p>
  <p>Die Wartung Der Anlagen Und Ein Ersatzteil-Service Sowie Professionelle Unterstützung Und Hilfestellung Bei Problemen Sind Für Uns Selbstverständliche Dienstleistungen.</p>
</div>
<div class="abs" role="img" aria-label="Team in einer Produktionshalle beim Händeschütteln" style="left:627px;top:2402px;width:495px;height:240px;background:linear-gradient(120deg,#c9ccd0,#9aa3ad 40%,#5e6a78 70%,#b6bcc2)"></div>

<!-- contact -->
<section class="abs contact">
  <div class="ph" role="img" aria-label="Produktionshalle mit Anlagen und Paletten"></div>
  <h2>KONTAKT</h2>
  <div class="field" style="left:556px;top:92px">Vorname</div>
  <div class="field" style="left:764px;top:92px">Nachname</div>
  <div class="field" style="left:556px;top:140px">Email</div>
  <div class="field" style="left:764px;top:140px">Telefonnummer</div>
  <div class="field" style="left:556px;top:228px;width:378px">Schreibe deine Nachricht...</div>
  <div class="send"><svg width="14" height="12" viewBox="0 0 24 20"><path d="M1 10L23 1l-5 18-7-6z" fill="#fff"/></svg>Senden</div>
</section>

<!-- footer -->
<footer class="abs footer">
  <h5 style="left:52px;top:30px">QUICKLINKS</h5>
  <div class="col" style="left:52px;top:47px">Unternehmen<br>Jobs / Karriere<br>Palettiertechnik</div>
  <div class="col" style="left:143px;top:47px">Packertechnik<br>Fördertechnik<br>Anlagen</div>
  <div class="col" style="left:228px;top:47px">Gebrauchtmaschinen<br>Aktuelles</div>
  <h5 style="left:361px;top:30px">PRODUKTE</h5>
  <div class="col" style="left:361px;top:47px">PALETTIERTECHNIK<br>PACKERTECHNIK</div>
  <div class="col" style="left:472px;top:47px">FÖRDERTECHNIK<br>GEBRAUCHTMASCHINEN</div>
  <h5 style="left:625px;top:30px">KONTAKT</h5>
  <div class="col" style="left:625px;top:52px;line-height:11px">KOLMATECH Maschinenbau GmbH<br>Am Werkhof 12<br>09100 Talheim</div>
  <div class="col" style="left:790px;top:47px">03400 / 200 - 0<br>03400 / 200 - 14<br>info@kolmatech.de</div>
  <div class="news-form">Abonnieren Sie den Newsletter
    <div class="box"><span class="in">Email</span><span class="go"><svg width="10" height="10" viewBox="0 0 20 20"><path d="M2 10h14M10 4l6 6-6 6" stroke="#fff" stroke-width="2.5" fill="none"/></svg></span></div>
  </div>
  <div class="copy">©2024. Kolmatech All rights reserved</div>
</footer>

</body>
</html>
```